Mobile Disc Jockey Service Brochure

We are looking for a brochure to showcase our Mobile DJ Business. It needs to be something professional looking and fit our target market of Weddings. We cater to events of all types but majority of our clients are brides looking for professional service at affordable prices.

Our website for reference: http://www.theclefcart.com/
facebook for reference: https://www.facebook.com/MarcusClefCart

I've uploaded a picture of us, our logo and some other photos that might be useful. Feel free to use additional stock photos that may be applicable to our project needs. Feel free to crop photos as necessary

I'd like this to be an 8 1/2" x 11" bifold, or trifold brochure, double sided. The front can be simple with our logo and phone number. Back can also be simple with a small logo and our website. I'd like one of the areas to focus on our bio and picture, and the other areas can describe our packages and what we offer as well as our mission statement

Some other information: We provide not only Professional and Enthusiastic DJ Services but we also do Uplighting as well as Event planning.

Target Market(s)

Weddings, Anniversary Parties, Birthdays, Themed Party

Industry/Entity Type

Business

Requirements
Must have
• Something describing our services like the following (feel free to rearrange the wording if necessary).
• All packages are hourly and custom built to fit your party needs. A list of our offerings includes:
• Cocktail music, dinner music, dance music
• Ultimate coordination of activities and unique event planning experience
• HD Sound
• LED Light Show
• Wireless Microphone System
• Unlimited choice of song titles from Digital to Vinyl
• Free travel within 50 miles - Travel outside of this is calculated with a fee per additional mile.
• Optional Services:
• Projector with Screen for Slide Shows & Movies
• Uplighting
• We provide a Fun & Easy to use web interface that walks you through the timeline of your event capturing every detail you desire, making planning fun! We guarantee you will hear everything you want, we have an endless music library as well as mobile internet so we can access any song you and your guests want instantly! In addition to the Online Event Planner, we offer unlimited consultations prior to your event to ensure face to face that you are getting everything you want and more.
• I'd like to see something featuring our services as well as our picture that I uploaded maybe cropped at the chest level or there abouts with this information:
• We are a husband and wife team. Marcus Holloway, the DJ has been providing custom soundtracks for events of all types for well over a decade. In 2011 his wife Tessa joined the team to handle all of the event coordination and logistics. Together we run the Clef Cart offering Professional DJ Services at a personal level. We enjoy working with clients to create the event that they deserve at an affordable price. Contact us today for your quote or visit us online.
• (555) 314-2286
• theclefcart@mailvo.com
• www.theclefcart.com
• www.facebook.com/MarcusClefCart
• Id also like something along the lines of:
• Your choice of DJ can make or break your event. The Clef Cart guarantees to go above and beyond to make your event flawless and unforgettable. We promise to provide nothing but the best, well within your budget. When it comes to Weddings, we recognize that your Wedding is the most important day of your life! We will work with you side by side to ensure that it's everything you have dreamed of and more. Let the experience we provide create a beautiful memory that will last a lifetime.
• (Mission Statement)
• Our mission is to provide high quality and affordable mobile DJ services that will fill your event with beautiful lifelong memories.
Nice to have
• Id like to see the picture of the bride and grandfather dancing put in there somewhere.
• Color Scheme should be a mix of greys, black, white, you can add color as needed to match photos/logo, etc.

```html
<!DOCTYPE html>
<html lang="en">
<head>
<meta charset="utf-8">
<title>The Clef Cart – Brochure Inside Spread</title>
<link href="https://fonts.googleapis.com/css2?family=Maven+Pro:wght@400;500;700&display=swap" rel="stylesheet">
<style>
  :root {
    --red: #b81400;
    --grey: #e4e4e4;
    --white: #ffffff;
    --ink: #111111;
    --frame: #555555;
    --caption: #1a1a1a;
  }
  * { box-sizing: border-box; margin: 0; padding: 0; }
  html, body { width: 1200px; height: 1000px; overflow: hidden; background: var(--white); }
  body { position: relative; font-family: "Maven Pro", Arial, sans-serif; color: var(--ink); }
  .abs { position: absolute; }

  /* Inside left spread */
  .spread-left { left: 50px; top: 124px; width: 550px; height: 711px; border: 2px solid var(--frame); background: var(--white); overflow: hidden; }
  .offer-col { left: 0; top: 0; width: 275px; height: 100%; background: var(--grey); }
  .offer-head { left: 0; top: 0; width: 275px; height: 188px; background: var(--red); color: var(--white); }
  .offer-head .kicker { position: absolute; left: 38px; top: 117px; font-size: 13px; letter-spacing: .5px; line-height: 1.15; }
  .offer-head .kicker strong { display: block; font-size: 17px; font-weight: 500; }
  .offer { position: absolute; width: 120px; text-align: center; font-size: 10px; font-weight: 700; }
  .offer svg { display: block; margin: 0 auto 6px; }
  .led-mark { font-size: 30px; font-weight: 700; color: var(--red); letter-spacing: 1px; line-height: 36px; display: block; margin-bottom: 4px; }
  .travel { left: 37px; top: 636px; width: 210px; font-size: 9px; line-height: 1.35; }
  .travel p + p { margin-top: 6px; }

  .hero-photo { left: 281px; top: 0; width: 267px; height: 188px; background: linear-gradient(160deg, #4f7a2a, #9bbd59 55%, #7a6a4a); }
  .copy-col { left: 310px; top: 208px; width: 200px; font-size: 9px; line-height: 1.32; }
  .section-title { font-size: 13px; font-weight: 500; line-height: 1.1; letter-spacing: .3px; }
  .section-title strong { display: block; font-size: 19px; font-weight: 500; }
  .copy-col .section-title { margin-bottom: 10px; }
  .copy-col p { margin-bottom: 6px; }
  .copy-col .gap { margin-top: 26px; }

  /* Inside right spread */
  .spread-right { left: 600px; top: 124px; width: 548px; height: 711px; background: var(--grey); overflow: hidden; }
  .gallery-head { left: 0; top: 0; width: 270px; height: 189px; background: var(--red); color: var(--white); }
  .gallery-head .section-title { position: absolute; left: 40px; top: 117px; }
  .photo { position: absolute; }
  .ph-dj { left: 279px; top: 80px; width: 189px; height: 150px; background: linear-gradient(135deg, #1d2a1a, #3e8d2e 50%, #1a1a1a); }
  .ph-bride { left: 97px; top: 202px; width: 173px; height: 131px; background: linear-gradient(160deg, #3a3030, #9a8f8a 50%, #2a2222); }
  .ph-party { left: 279px; top: 242px; width: 231px; height: 148px; background: linear-gradient(140deg, #5a3f4a, #a88aa0 45%, #2e2630); }
  .ph-dance { left: 40px; top: 342px; width: 230px; height: 155px; background: linear-gradient(150deg, #2a2624, #6b5d56 50%, #1d1a19); }
  .ph-lights { left: 281px; top: 399px; width: 202px; height: 98px; background: radial-gradient(circle at 40% 50%, #6d7ab8, #2f3f7a 45%, #111a33); }
  .testi-title { left: 40px; top: 526px; }
  .testi-band { left: 0; top: 565px; width: 548px; height: 146px; background: var(--red); color: var(--white); }
  .avatar { position: absolute; top: 10px; width: 72px; height: 72px; border: 3px solid var(--white); }
  .av-1 { left: 39px; background: linear-gradient(160deg, #7a6a5a, #c9b9a8); }
  .av-2 { left: 277px; background: linear-gradient(160deg, #5a4a3a, #a9a090); }
  .who { position: absolute; top: 91px; font-size: 8px; line-height: 1.35; }
  .who strong { display: block; font-weight: 700; }
  .quote { position: absolute; top: 12px; font-size: 9px; line-height: 1.3; }
  .q-1 { left: 127px; width: 135px; }
  .q-2 { left: 365px; width: 130px; }

  .caption { top: 857px; font-family: Arial, Helvetica, sans-serif; font-size: 18px; color: var(--caption); width: 300px; text-align: center; }
</style>
</head>
<body>

<section class="abs spread-left">
  <div class="abs offer-col">
    <div class="abs offer-head">
      <h2 class="kicker">A LIST OF OUR<strong>OFFERINGS</strong>INCLUDES:</h2>
    </div>

    <div class="offer" style="left:21px;top:206px">
      <svg width="40" height="38" viewBox="0 0 40 38" fill="none" stroke="#b81400" stroke-width="2"><path d="M8 6h10l-3 12h-4z M13 18v14 M8 32h10 M22 6h10l-2 12h-5z M27 18v14 M22 32h10"/><circle cx="20" cy="3" r="1.5" fill="#b81400"/></svg>
      Cocktail music
    </div>
    <div class="offer" style="left:148px;top:206px">
      <svg width="44" height="38" viewBox="0 0 44 38"><circle cx="22" cy="19" r="14" fill="#b81400"/><circle cx="22" cy="19" r="8" fill="none" stroke="#fff" stroke-width="1.5"/><rect x="2" y="4" width="3" height="30" fill="#b81400"/><rect x="39" y="4" width="3" height="30" fill="#b81400"/></svg>
      Dinner music
    </div>
    <div class="offer" style="left:21px;top:283px">
      <svg role="img" aria-label="Dancing couple icon" width="40" height="46" viewBox="0 0 40 46"><circle cx="20" cy="23" r="18" fill="#b81400"/></svg>
      Dance music
    </div>
    <div class="offer" style="left:148px;top:290px">
      <svg width="34" height="36" viewBox="0 0 34 36"><rect x="1" y="5" width="32" height="30" fill="#b81400"/><rect x="8" y="1" width="3" height="8" fill="#b81400"/><rect x="23" y="1" width="3" height="8" fill="#b81400"/><g fill="#fff"><rect x="6" y="14" width="5" height="4"/><rect x="14" y="14" width="5" height="4"/><rect x="22" y="14" width="5" height="4"/><rect x="6" y="22" width="5" height="4"/><rect x="14" y="22" width="5" height="4"/><rect x="22" y="22" width="5" height="4"/></g></svg>
      Event planning
    </div>
    <div class="offer" style="left:21px;top:373px">
      <svg width="50" height="38" viewBox="0 0 50 38" fill="none" stroke="#b81400" stroke-width="3"><path d="M8 28V18a17 17 0 0 1 34 0v10"/><rect x="4" y="22" width="8" height="14" fill="#b81400"/><rect x="38" y="22" width="8" height="14" fill="#b81400"/><text x="25" y="34" text-anchor="middle" font-family="Maven Pro, sans-serif" font-weight="700" font-size="14" fill="#b81400" stroke="none">HD</text></svg>
      HD Sound
    </div>
    <div class="offer" style="left:148px;top:377px">
      <span class="led-mark">LED</span>
      LED Light Show
    </div>
    <div class="offer" style="left:21px;top:446px">
      <svg width="44" height="44" viewBox="0 0 44 44"><circle cx="31" cy="12" r="10" fill="#b81400"/><path d="M24 18L6 38l3 3 20-17z" fill="#b81400"/></svg>
      Wireless Microphone
    </div>
    <div class="offer" style="left:148px;top:449px">
      <svg width="54" height="42" viewBox="0 0 54 42" stroke="#b81400" fill="#b81400"><g stroke-width="1"><line x1="2" y1="10" x2="52" y2="10"/><line x1="2" y1="18" x2="52" y2="18"/><line x1="2" y1="26" x2="52" y2="26"/><line x1="2" y1="34" x2="52" y2="34"/></g><ellipse cx="10" cy="30" rx="4" ry="3"/><rect x="13" y="6" width="2" height="24"/><ellipse cx="42" cy="34" rx="4" ry="3"/><rect x="45" y="12" width="2" height="22"/><text x="27" y="34" text-anchor="middle" font-size="28" stroke="none">&#119070;</text></svg>
      Unlimited of song
    </div>
    <div class="offer" style="left:21px;top:546px">
      <svg width="48" height="30" viewBox="0 0 48 30"><rect x="2" y="6" width="44" height="20" rx="4" fill="#b81400"/><circle cx="30" cy="16" r="7" fill="#fff"/><circle cx="30" cy="16" r="4" fill="#b81400"/><rect x="8" y="12" width="10" height="2" fill="#fff"/><rect x="8" y="17" width="10" height="2" fill="#fff"/></svg>
      Projector with Screen
    </div>
    <div class="offer" style="left:148px;top:543px">
      <svg width="36" height="36" viewBox="0 0 36 36"><circle cx="18" cy="18" r="17" fill="#b81400"/><g fill="#fff"><circle cx="12" cy="12" r="1.8"/><circle cx="18" cy="10" r="1.8"/><circle cx="24" cy="12" r="1.8"/><circle cx="10" cy="18" r="1.8"/><circle cx="16" cy="17" r="1.8"/><circle cx="22" cy="18" r="1.8"/><circle cx="27" cy="19" r="1.8"/><circle cx="13" cy="24" r="1.8"/><circle cx="19" cy="24" r="1.8"/><circle cx="25" cy="25" r="1.8"/></g></svg>
      Uplighting
    </div>

    <div class="abs travel">
      <p>Free travel*</p>
      <p>within 50 miles - Travel outside of this is calculated with a fee per additional mile.</p>
    </div>
  </div>

  <div class="abs hero-photo" role="img" aria-label="Bride and groom dancing on a forest path"></div>

  <div class="abs copy-col">
    <h2 class="section-title">MISSION<strong>STATEMENT</strong></h2>
    <p>Our mission is to provide high quality and affordable mobile DJ services that will fill your event with beautiful lifelong memories.</p>

    <h2 class="section-title gap">MAKE YOUR EVENT<strong>MEMORALE</strong></h2>
    <p>Your choice of DJ can make or break your event. The Clef Cart guarantees to go above and beyond to make your event flawless and unforgettable. We promise to provide nothing but the best, well within your budget.</p>
    <p>When it comes to Weddings, we recognize that your Wedding is the most important day of your life! We will work with you side by side to ensure that it's everything you have dreamed of and more. Let our experience create a memory for a lifetime, you will not be disappointed!</p>
    <p>We provide a Fun &amp; Easy to use web interface that walks you through the timeline of your event capturing every detail you desire, making planning fun! We guarantee you will hear everything you want, we have an endless music library as well as mobile internet so we can access any song you and your guests want instantly!</p>
    <p>In addition to the Online Event Planner, we offer unlimited consultations prior to your event to ensure face to face that you are getting everything you want and more.</p>
  </div>
</section>

<section class="abs spread-right">
  <div class="abs gallery-head">
    <h2 class="section-title">PHOTO<strong>GALLERY</strong></h2>
  </div>
  <div class="photo ph-dj" role="img" aria-label="DJ booth with green lighting and dance floor light spots"></div>
  <div class="photo ph-bride" role="img" aria-label="Bride dancing with guests at a reception"></div>
  <div class="photo ph-party" role="img" aria-label="Guests dancing under purple uplighting with balloons"></div>
  <div class="photo ph-dance" role="img" aria-label="Couples dancing in a reception hall"></div>
  <div class="photo ph-lights" role="img" aria-label="Colourful light show across a dance floor"></div>

  <h2 class="abs section-title testi-title">CLIENT<strong>TESTIMONIALS</strong></h2>
  <div class="abs testi-band">
    <div class="avatar av-1" role="img" aria-label="Client photo"></div>
    <div class="who" style="left:39px"><strong>Dalton Reyes</strong>October 30, 2014</div>
    <p class="quote q-1">Thank you guys so much for coming out. My wife and our family had tons of fun and you and your wife make a really good team! Definitely will be referring you guys because you guys have skill and good personalities!</p>

    <div class="avatar av-2" role="img" aria-label="Client photo"></div>
    <div class="who" style="left:281px"><strong>Carla Brightwell</strong>June 4, 2014</div>
    <p class="quote q-2">Hosted my mom party and did a great job my family was impressed. Thanks great times.</p>
  </div>
</section>

<p class="abs caption" style="left:175px">Option 2_Inside Left</p>
<p class="abs caption" style="left:749px">Option 2_Inside Right</p>

</body>
</html>
```